Flalzflyer-Design (Folder)
Da für uns neben einem guten Design ein angenehmer und konstruktiver Dialog sowie Verlässlichkeit von hoher Bedeutung ist, sind wir sehr froh auf dieser Plattform auf "brightloom" gestoßen zu sein. Wir sagen ganz herzlich DANKE!!
Zielgruppe
Zielgruppe im Bereich der Vermietung sind Alleinreisende oder als Paar verreisende Natur- und Nordsee verbundene Feriengäste (ü30) mit dem Urlaubsziel 'Sylt', welche eine persönlich und mit besonderem Schick eingerichtet Ferienwohnung/Ferienapartment in zentraler Lage in Westerland suchen und die es als positiven bzw. interessanten Aspekt sehen, dass die Ferienwohnungen direkt von uns Insulaner angeboten werden und wir als Sylter Familie ebenfalls Vor-Ort mit dem Urlaubern unter dem selben Dach leben (wenn auch nicht in der derselben Wohnung ;) ), ganz gemäß unserem Slogan 'Nordseeurlaub unter einem Dach mit Insulanern'
Aufgabenstellung
Es soll ein Falzflyer (Folder) mit Wickelfalz (siehe ggf. https://www.druckwerk-nord.de/werbemittel/folder.html) designed werden (4/4-farbig Euroskala). Bestehend aus einem Papier Format DIN A4 mit zwei Falzen, sodass sich bei Berücksichtigung von Vor- u. Rückseite 6 Seiten ergeben. Die wesentlichen Texte/Inhalte/Informationen, finden sich hier: https://www.quartiersuche-online.de/481926/ . Neben dem Ferienapartment 'Kompass' w ird von uns die Ferienwohnung 'Wadlen' (friesisch für Seestern) angeboten, ebenfalls im Morgenlicht Sylt HOUSE (EST. 2017).
Preisangaben können unberücksichtigt beliben, da sie dem Folder später über eine gesondere Einlage beigelegt werden sollen.
Im Rahmen des Dateiupload bei entwurfsmarkt werden nur einige der möglichen Fotos bereitgestellt. Sie sollen als Auswahlmöglichkeit dienen. Welche der Fotos Verwendung finden oder nach weiteren nachgefragt wird, soll in Abhängigkeit mit dem Gesamtdesign stehen und zunächst von Ihnen entschieden werden, um ein möglichst ansprechenden und harmonischen Folder kreieren zu können.

```html
<!DOCTYPE html>
<html lang="de">
<head>
<meta charset="utf-8">
<title>Morgenlicht Sylt HOUSE – Folder</title>
<link href="https://fonts.googleapis.com/css2?family=Lato:wght@400;700&family=Arimo:wght@400;700&family=Sacramento&display=swap" rel="stylesheet">
<style>
:root{
  --blue:#3a93c3;
  --ink:#3f3f3f;
  --ink-soft:#555;
  --band:#2b2b2b;
  --paper:#ffffff;
}
*{margin:0;padding:0;box-sizing:border-box}
html,body{width:832px;height:1200px;overflow:hidden;background:var(--paper)}
.folder{position:relative;width:832px;height:1200px;font-family:'Lato',sans-serif;color:var(--ink);overflow:hidden}
.abs{position:absolute}
.photo{position:absolute}
.script{font-family:'Sacramento',cursive;color:var(--blue);font-weight:400;line-height:1;white-space:nowrap;transform:scaleY(1.35);transform-origin:left top}
.script.centered{transform-origin:center top}
.band{position:absolute;left:0;top:590px;width:832px;height:16px;background:var(--band)}
/* top left */
.cozy-title{left:14px;top:270px;width:246px;text-align:center;font-size:24px}
.cozy-sub{left:14px;top:302px;width:246px;text-align:center;font-size:12.5px;letter-spacing:.2px}
/* top middle */
.visit{left:287px;top:256px;font-size:14.5px;line-height:19px}
.visit b{font-weight:700}
.visit-copy{left:287px;top:300px;width:252px;font-size:8.6px;line-height:13.6px}
.visit-copy p{margin-bottom:7.5px}
.dash{left:287px;top:444px;width:249px;border-top:1.2px dashed var(--blue)}
.contact{left:287px;top:452px;width:260px;font-size:8.6px;line-height:12.6px}
.contact .gap{height:12px}
/* top right */
.cover-title{left:563px;top:412px;width:255px;text-align:center;font-size:23px}
.cover-name{left:563px;top:449px;width:255px;text-align:center;font-size:13.5px;font-weight:700;line-height:15px}
.cover-est{left:563px;top:464px;width:255px;text-align:center;font-size:10.5px}
.welcome{left:563px;top:506px;width:255px;text-align:center;font-size:17px;line-height:19px}
.welcome b{font-weight:700}
/* bottom */
.bottom{font-family:'Arimo',sans-serif;font-size:8.6px;line-height:12.6px;color:var(--ink-soft)}
.head{font-size:22px;top:628px}
.copy p{margin-bottom:12.5px}
.copy .lead{font-weight:700;color:var(--ink)}
.icons{display:flex;position:absolute;top:1124px}
.icon{width:50.5px;text-align:center;font-family:'Lato',sans-serif;font-size:6.3px;line-height:8.3px;color:var(--ink-soft)}
.icon svg{display:block;margin:0 auto 5px;width:36px;height:36px}
</style>
</head>
<body>
<svg width="0" height="0" style="position:absolute">
  <defs>
    <symbol id="ring" viewBox="0 0 36 36"><circle cx="18" cy="18" r="16.6" fill="none" stroke="#3a93c3" stroke-width="2"/></symbol>
    <symbol id="i-wifi" viewBox="0 0 36 36"><use href="#ring"/><g fill="none" stroke="#3a93c3" stroke-width="2.2" stroke-linecap="round"><path d="M9 15a13 13 0 0 1 18 0"/><path d="M12 18.5a8.5 8.5 0 0 1 12 0"/><path d="M15 22a4 4 0 0 1 6 0"/></g><circle cx="18" cy="25" r="1.7" fill="#3a93c3"/></symbol>
    <symbol id="i-nosmoke" viewBox="0 0 36 36"><use href="#ring"/><rect x="9" y="19" width="16" height="3.5" fill="#3a93c3"/><rect x="26" y="19" width="2" height="3.5" fill="#3a93c3"/><path d="M24 11c2 2-1 3 1 6M27 11c2 2-1 3 1 6" fill="none" stroke="#3a93c3" stroke-width="1.4"/><path d="M8 9l20 19" stroke="#3a93c3" stroke-width="2.2"/></symbol>
    <symbol id="i-chair" viewBox="0 0 36 36"><use href="#ring"/><g fill="none" stroke="#3a93c3" stroke-width="1.6"><path d="M11 26V14a7 5 0 0 1 14 0v12z"/><path d="M13 17h10M13 20h10M13 23h10"/></g></symbol>
    <symbol id="i-dish" viewBox="0 0 36 36"><use href="#ring"/><g fill="none" stroke="#3a93c3" stroke-width="1.6"><rect x="11" y="9" width="14" height="18" rx="1.5"/><path d="M11 13h14"/><circle cx="18" cy="21" r="3.5"/></g></symbol>
    <symbol id="i-bed" viewBox="0 0 36 36"><use href="#ring"/><g fill="#3a93c3"><rect x="9" y="12" width="2" height="14"/><rect x="9" y="20" width="18" height="3"/><rect x="25" y="18" width="2" height="8"/><circle cx="14" cy="17" r="2"/><rect x="17" y="15.5" width="9" height="4" rx="1"/></g></symbol>
    <symbol id="i-tv" viewBox="0 0 36 36"><use href="#ring"/><g fill="none" stroke="#3a93c3" stroke-width="1.8"><rect x="9" y="11" width="18" height="12" rx="1"/><path d="M18 23v3M13 27h10"/></g></symbol>
  </defs>
</svg>

<main class="folder">

  <!-- inside: top left panel -->
  <section class="panel panel-interior">
    <div class="photo" style="left:14px;top:14px;width:85px;height:121px;background:linear-gradient(160deg,#eeece8,#d8d4cc)" role="img" aria-label="Weiße Kommode mit blauem Wolldekor an der Wand"></div>
    <div class="photo" style="left:102px;top:14px;width:158px;height:121px;background:linear-gradient(160deg,#7c5a3a,#a4733f 55%,#6d3f38)" role="img" aria-label="Holzregal mit Sylt-Schriftzug und Muscheldeko"></div>
    <div class="photo" style="left:14px;top:138px;width:161px;height:121px;background:linear-gradient(180deg,#1e4a4e,#a7a296 45%,#4b3a30)" role="img" aria-label="Fenster mit Rollo und Kerzen auf dem Tisch"></div>
    <div class="photo" style="left:177px;top:138px;width:83px;height:121px;background:linear-gradient(180deg,#dfe6e6,#7fb0b7 70%,#d5dfdf)" role="img" aria-label="Glasregal mit Tassen und Gläsern"></div>
    <div class="abs script centered cozy-title">Gemütlich &amp; mit Liebe</div>
    <div class="abs cozy-sub">ZUM DETAIL EINGERICHTET</div>
    <div class="photo" style="left:14px;top:331px;width:164px;height:122px;background:linear-gradient(180deg,#c7cdc6,#d8c52e 55%,#8e7652)" role="img" aria-label="Pantryküche mit gelber Wand und Dünenbild"></div>
    <div class="photo" style="left:181px;top:331px;width:79px;height:122px;background:linear-gradient(180deg,#e6e2dc,#8b7a6c 60%,#d9d2c8)" role="img" aria-label="Fenster mit Vorhängen und Bett"></div>
    <div class="photo" style="left:14px;top:456px;width:101px;height:122px;background:linear-gradient(90deg,#d8d2c8,#c9a735 80%)" role="img" aria-label="Holzherz an weißer Garderobe"></div>
    <div class="photo" style="left:118px;top:456px;width:142px;height:122px;background:linear-gradient(180deg,#e8e4de,#b7b0a6 60%,#6a6561)" role="img" aria-label="Wohnbereich mit blauem Tisch und Sofa"></div>
  </section>

  <!-- inside: top middle panel -->
  <section class="panel panel-visit">
    <div class="photo" style="left:287px;top:14px;width:123px;height:225px;background:linear-gradient(180deg,#3a79c7 0%,#e8e4dc 30%,#c9a46a 55%,#5b7a3a 75%,#a04a3a)" role="img" aria-label="Hausfassade mit gepflastertem Weg und Garten"></div>
    <div class="photo" style="left:413px;top:14px;width:123px;height:110px;background:linear-gradient(180deg,#4e6a3a,#6a6fb0 45%,#dcdce4 85%)" role="img" aria-label="Blaue Hortensien und Tassen auf einem Gartentisch"></div>
    <div class="photo" style="left:413px;top:127px;width:123px;height:112px;background:linear-gradient(180deg,#e6e9ec,#b7bcc1 45%,#5e6a6c 80%,#3e4446)" role="img" aria-label="Schwimmer im Meerwasser-Schwimmbecken am Meer"></div>
    <div class="abs visit"><b>BESUCHEN SIE UNS</b><br>AUF SYLT.</div>
    <div class="abs visit-copy">
      <p>Das Morgenlicht Sylt House (est. 2017) ist in Nachbarschaft des denkmalgeschützten Westerländer Polizeigebäudes (ehem. Amtsgericht) gelegen. Die vorteilhafte Lage ist damit zentral aber ruhig in 2. Reihe in Alt-Westerland.</p>
      <p>Der Bahnhof ist ca. 4-5 Gehminuten, die Fußgängerzone/Friedrichstr. mit div. Einkaufsmöglichkeiten und Restaurants/Cafés ca. 7 Min. und der Strand/die Kurpromenade ca. 12 Min. entfernt. Auch das Inselbad Westerland, das Vitalzentrum (Wellness) o. die Spielbank sind nah.</p>
    </div>
    <div class="abs dash"></div>
    <address class="abs contact" style="font-style:normal">
      Familie Morgenlicht<br>
      <b>Morgenlicht Sylt HOUSE (EST. 2017)</b><br>
      Dünenweg 14b, Westerland
      <div class="gap"></div>
      <b>Wir sind für Sie da</b> · &nbsp;Mo - So &nbsp;&nbsp;9.00 - 21.00<br>
      Telefon:+49 (0)4651 - 300 5127 · Mobil: +49 (0)171 - 508 2619<br>
      eMail: sylt@morgenlicht-sylt.net<br>
      Belegungskalender: sylt.morgenlicht-sylt.net<br>
      Mehr Fotos + Preise finden Sie auf: quartiersuche-online.de<br>
      =&gt; Wohin: Morgenlicht Sylt
    </address>
  </section>

  <!-- cover panel -->
  <section class="panel panel-cover">
    <div class="photo" style="left:563px;top:14px;width:255px;height:372px;background:linear-gradient(180deg,#4c8ed6 0%,#dfe9f3 22%,#8fb4d6 40%,#2d5b72 45%,#cfd9dc 52%,#e4d6bf 68%,#8a7a5e 100%)" role="img" aria-label="Strand mit Rettungsturm, Fahne und blau-weißen Strandkörben"></div>
    <div class="abs script centered cover-title">Nordseeurlaub bei Insulanern</div>
    <div class="abs cover-name">Morgenlicht Sylt HOUSE</div>
    <div class="abs cover-est">(EST. 2017)</div>
    <div class="abs welcome">HERZLICH WILLKOMMEN<br><b>BEI FAMILIE MORGENLICHT!</b></div>
  </section>

  <div class="band"></div>

  <!-- bottom left: apartment Kompass -->
  <section class="panel bottom">
    <h2 class="abs script head" style="left:14px">Ferienapartment 'Kompass'</h2>
    <div class="photo" style="left:14px;top:664px;width:126px;height:121px;background:linear-gradient(180deg,#dcd7cf,#b79a7a 55%,#5d4a3d)" role="img" aria-label="Schlafzimmer mit Einzelbett und Nachttisch"></div>
    <div class="photo" style="left:143px;top:664px;width:125px;height:121px;background:linear-gradient(180deg,#e6e2dc,#c7c2ba 50%,#4a4544)" role="img" aria-label="Wohnbereich mit Sofa und Kissen"></div>
    <div class="abs copy" style="left:14px;top:793px;width:256px"><p>Das Apartment ist seniorengerecht, ebenerdig, kurze Wege, Ansprechpartner im Haus, Bahnhof Westerland fussläufig 5 Min.</p></div>
    <div class="photo" style="left:52px;top:830px;width:205px;height:112px;background:linear-gradient(180deg,#eeeed8,#dde8f1)" role="img" aria-label="Grundriss Apartment Kompass im Erdgeschoss mit Außenbereich"></div>
    <div class="abs copy" style="left:14px;top:957px;width:256px">
      <p><span class="lead">Wer Meer hat, braucht weniger, sagt man.</span><br>Die Zimmer persönlich und mit Geschick gestaltet, zeitgemäße Wohneinrichtung, modernes ebenerdiges Duschbad, hochwertige Pantryküche, Smart-TV, Wlan, ansprechendes und vollständiges Geschirr, Außenbereich sowie der persönlichen Nähe zu uns Insulanern.</p>
      <p>Das App. eignet sich für einen längeren Urlaub besonders für 1 Person. Es steht ein Einzelbett im kl. Schlafzimmer zur Verfügung. Für einen Aufenthalt von einigen Tagen haben 2 Pers. ebenfalls eine passend schöne Unterkunft (Schlafmöglichkeit auf komfortablen Schlafsofa mit Lattenrost).</p>
    </div>
    <div class="icons" style="left:10px">
      <div class="icon"><svg><use href="#i-wifi"/></svg>kostenloses<br>WLAN</div>
      <div class="icon"><svg><use href="#i-nosmoke"/></svg>Nichtraucher<br>Wohnung</div>
      <div class="icon"><svg><use href="#i-chair"/></svg>Strandkorb<br>vorhanden</div>
      <div class="icon"><svg><use href="#i-dish"/></svg>Geschirrspüler<br>vorhanden</div>
      <div class="icon"><svg><use href="#i-bed"/></svg>Bettwäsche &amp;<br>Handtücher</div>
    </div>
  </section>

  <!-- bottom middle: about us -->
  <section class="panel bottom">
    <h2 class="abs script head" style="left:296px">Wer sind wir</h2>
    <div class="abs copy" style="left:296px;top:668px;width:250px"><p>Wir sind eine 3-köpfige Familie, die ganzjährig im Morgenlicht Sylt HOUSE (Est. 2017) lebt und auf Wunsch gerne helfend mit Urlaubstipps und Klönschnack zur Verfügung steht. Unsere Tochter geht in Westerland zur Schule.</p></div>
    <h2 class="abs script" style="left:296px;top:730px;font-size:22px">Warum sind wir Gastgeber</h2>
    <div class="abs copy" style="left:296px;top:770px;width:250px"><p>Weil wir als offene Menschen neue Begegnungen schätzen und so unseren Traum - ganzjährig auf Sylt zu leben - in die Tat umsetzen können.</p></div>
    <div class="photo" style="left:296px;top:814px;width:80px;height:122px;background:linear-gradient(160deg,#c9c1b6,#a89d8f)" role="img" aria-label="In den Sand geschriebene Buchstaben"></div>
    <div class="photo" style="left:380px;top:814px;width:165px;height:122px;background:linear-gradient(180deg,#6aa0d8,#cfe1ef 40%,#7e9aa8 50%,#d9c7a2 65%,#8c9a52)" role="img" aria-label="Strand und Dünen am Meer"></div>
    <div class="photo" style="left:296px;top:939px;width:148px;height:98px;background:linear-gradient(180deg,#4c7fb8,#dfe6ee 45%,#7f8a8e 60%,#cfc4b2)" role="img" aria-label="Spaziergänger am weiten Sandstrand"></div>
    <div class="photo" style="left:447px;top:939px;width:98px;height:98px;background:linear-gradient(180deg,#3d5c80,#e2a25a 55%,#3b2e26)" role="img" aria-label="Sonnenuntergang über den Dünen"></div>
    <h2 class="abs script" style="left:296px;top:1055px;font-size:22px">Unser Service für Sie</h2>
    <div class="abs copy" style="left:296px;top:1096px;width:250px">
      <p>Kostenloser Hol-/Bringservice Bahnhof Westerland nach Absprache möglich.</p>
      <p>Das Wäschepaket beinhaltet: Bettwäsche, Laken, Handtuch (2x), Duschtuch, Badvorleger, Geschirrtuch.</p>
      <p>Endreinigung inklusive.</p>
    </div>
  </section>

  <!-- bottom right: apartment Wadlen -->
  <section class="panel bottom">
    <h2 class="abs script head" style="left:572px">Ferienwohnung 'Wadlen'</h2>
    <div class="photo" style="left:572px;top:664px;width:123px;height:121px;background:linear-gradient(180deg,#d8d8dc,#6a5a52 45%,#e0dcd6 70%,#c44a42)" role="img" aria-label="Schlafzimmer mit Doppelbett und bunter Bettwäsche"></div>
    <div class="photo" style="left:698px;top:664px;width:120px;height:121px;background:linear-gradient(180deg,#e8e6e2,#6b4f3d 45%,#d8d8d6 75%,#4e7a4e)" role="img" aria-label="Modernes Duschbad mit Fenster"></div>
    <div class="abs copy" style="left:572px;top:793px;width:248px"><p>Das Apartment ist seniorengerecht, ebenerdig, kurze Wege, Ansprechpartner im Haus, Bahnhof Westerland fussläufig.</p></div>
    <div class="photo" style="left:625px;top:830px;width:139px;height:121px;background:linear-gradient(180deg,#f2c2b2,#eeb9a8)" role="img" aria-label="Grundriss Ferienwohnung Wadlen im 1. Obergeschoss"></div>
    <div class="abs copy" style="left:572px;top:957px;width:248px">
      <p><span class="lead">Wer Meer hat, braucht weniger, sagt man.</span><br>Die Zimmer persönlich und mit Geschick gestaltet, zeitgemäße Wohneinrichtung, modernes ebenerdiges Duschbad, hochwertige Pantryküche, Smart-TV, Wlan, ansprechendes und vollständiges Geschirr, Außenbereich sowie der persönlichen Nähe zu uns Insulanern.</p>
      <p>Das App. eignet sich für einen längeren Urlaub besonders für 1 Person. Es steht ein Einzelbett im kl. Schlafzimmer zur Verfügung. Für einen Aufenthalt von einigen Tagen haben 2 Pers. ebenfalls eine passend schöne Unterkunft (Schlafmöglichkeit auf komfortablen Schlafsofa mit Lattenrost).</p>
    </div>
    <div class="icons" style="left:568px;top:1120px">
      <div class="icon"><svg><use href="#i-wifi"/></svg>kostenloses<br>WLAN</div>
      <div class="icon"><svg><use href="#i-nosmoke"/></svg>Nichtraucher<br>Wohnung</div>
      <div class="icon"><svg><use href="#i-tv"/></svg>Smart TV<br>vorhanden</div>
      <div class="icon"><svg><use href="#i-dish"/></svg>Geschirrspüler<br>vorhanden</div>
      <div class="icon"><svg><use href="#i-bed"/></svg>Bettwäsche &amp;<br>Handtücher</div>
    </div>
  </section>

</main>
</body>
</html>
```